Northfield Builders Guild Business card

We are looking for a new business card design with photo included.
Our business is a nonprofit construction contractor membership organization. We offer business education, assist with business setup and licensing, provide safety training, and provide a member directory.
URL: www.builderslinkguild.org
Color code:
CMYK: 0 cyan, 42 magenta, 100 yellow, 0 black for Print.
Hexidecimal: #FF9900
RGB: R 255; G 153; B 0

```html
<!DOCTYPE html>
<html lang="en">
<head>
<meta charset="UTF-8">
<title>Northfield Builders Guild – Business Card</title>
<link href="https://fonts.googleapis.com/css2?family=Poppins:wght@400;500;600;700&display=swap" rel="stylesheet">
<style>
  :root {
    --orange: #FF9900;
    --charcoal: #2c2c2e;
    --paper: #f1f1f3;
    --ink: #2a2a2a;
    --light-text: #e9e9e9;
    --backdrop: #1b1b1c;
  }
  * { box-sizing: border-box; margin: 0; padding: 0; }
  html, body {
    width: 1200px; height: 900px; overflow: hidden;
    background: var(--backdrop);
    font-family: "Poppins", sans-serif;
  }
  .stage {
    width: 1200px; height: 900px;
    display: flex; flex-direction: column; align-items: center; justify-content: center;
    gap: 44px;
  }
  .card {
    position: relative;
    width: 600px; height: 343px;
    background: var(--charcoal);
    overflow: hidden;
    border-bottom: 3px solid var(--orange);
    border-left: 2px solid var(--orange);
  }

  /* Front */
  .card-front .header {
    position: absolute; left: 0; top: 0; width: 100%; height: 128px;
    background: var(--paper);
    border-bottom: 3px solid var(--orange);
  }
  .person-name {
    position: absolute; left: 60px; top: 52px;
    color: var(--orange); font-weight: 600; font-size: 22px; letter-spacing: 0.2px;
  }
  .person-title {
    position: absolute; left: 60px; top: 84px;
    color: var(--ink); font-size: 13px;
  }
  .portrait {
    position: absolute; right: 60px; top: 38px;
    width: 138px; height: 138px; border-radius: 50%;
    border: 3px solid var(--orange);
    background: radial-gradient(circle at 50% 40%, #8a6a58 0%, #4a3a34 45%, #2b2322 100%);
  }
  .contact-list {
    position: absolute; left: 64px; top: 176px;
    list-style: none; color: var(--light-text); font-size: 13.5px; line-height: 20px;
  }
  .contact-list li { display: flex; align-items: center; gap: 10px; }
  .contact-list svg { width: 13px; height: 13px; flex: none; }
  .address {
    position: absolute; left: 64px; top: 256px;
    color: var(--light-text); font-size: 13.5px; line-height: 21px;
  }

  /* Back */
  .guild-name {
    position: absolute; right: 70px; top: 112px; width: 330px;
    text-align: right;
    color: var(--orange); font-weight: 700; font-size: 33px; line-height: 38px;
    text-transform: uppercase;
  }
  .service-band {
    position: absolute; left: 0; right: 0; top: 230px; height: 30px;
    background: var(--orange);
    display: flex; align-items: center; justify-content: center; gap: 8px;
    color: var(--charcoal); font-size: 12.5px; font-weight: 500;
  }
  .service-band .divider { opacity: 0.8; }
</style>
</head>
<body>
<main class="stage">

  <section class="card card-front">
    <div class="header"></div>
    <h1 class="person-name">Jordan Ellery</h1>
    <p class="person-title">Director</p>
    <div class="portrait" role="img" aria-label="Portrait photo of the director"></div>

    <ul class="contact-list">
      <li>
        <svg viewBox="0 0 24 24" fill="none" stroke="var(--orange)" stroke-width="2"><path d="M22 16.9v3a2 2 0 0 1-2.2 2 19.8 19.8 0 0 1-8.6-3.1 19.5 19.5 0 0 1-6-6A19.8 19.8 0 0 1 2.1 4.2 2 2 0 0 1 4.1 2h3a2 2 0 0 1 2 1.7c.1 1 .4 1.9.7 2.8a2 2 0 0 1-.5 2.1L8 9.9a16 16 0 0 0 6 6l1.3-1.3a2 2 0 0 1 2.1-.4c.9.3 1.8.6 2.8.7a2 2 0 0 1 1.7 2z"/></svg>
        (555) 014-2290
      </li>
      <li>
        <svg viewBox="0 0 24 24" fill="none" stroke="var(--orange)" stroke-width="2"><rect x="2" y="5" width="20" height="14" rx="1"/><path d="M2 6l10 7 10-7"/></svg>
        info@builderslinkguild.org
      </li>
      <li>
        <svg viewBox="0 0 24 24" fill="none" stroke="var(--orange)" stroke-width="2"><circle cx="12" cy="12" r="10"/><path d="M2 12h20M12 2a15 15 0 0 1 0 20M12 2a15 15 0 0 0 0 20"/></svg>
        builderslinkguild.org
      </li>
    </ul>

    <p class="address">2480 Millbrook Avenue<br>Fairhaven, OR 97000</p>
  </section>

  <section class="card card-back">
    <h2 class="guild-name">Northfield Builders Guild</h2>
    <div class="service-band">
      <span>Technical Assistance</span><span class="divider">|</span>
      <span>Contractor Education</span><span class="divider">|</span>
      <span>Safety &amp; Compliance</span><span class="divider">|</span>
      <span>Contractor Directory</span>
    </div>
  </section>

</main>
</body>
</html>
```